VELTAR WEBSITE

need to create a new website for VELTAR ltd
the company deals with all aspects of safety products & safety wear
we need a simple website to show
ideas can be taken from following website whose products we shall distribute in kenya
www.kwr.co.uk
www.dorvik.eu
www.brimtoolsupplyco.com
www.gardvalewerks.co.za

we need following tabs
1) home - basic company information
2) products - broken down to following categories ie gloves, head protection, ear protection, mouth protection, foot protection
3) contacts

the company profile is a reputable company dealing with all aspects of safety, HSE (health and safety equipment), and PPE (personal protective equipment)

the website should have the dorvik logo for which we are an authorized distributor.
the dorvi industrial range writeup can be picked from their website
Updates

Dear Designers, i shall be able to choose a final design in 2 weeks, sorry i have not been able to finalise this due to a personal reason

Target Market(s)

the buyers are all types of industry who care for their employees safety

Industry/Entity Type

Industrial

Requirements
Must have
• clean look, fresh look, user freindly
Nice to have
• clear images, quick links etc

```html
<!DOCTYPE html>
<html lang="en">
<head>
<meta charset="utf-8">
<title>VELTAR – Safety Products</title>
<link href="https://fonts.googleapis.com/css2?family=Lato:wght@400;700;900&display=swap" rel="stylesheet">
<style>
:root{
  --yellow:#f9ae1d;
  --navy:#163a4c;
  --ink:#23323b;
  --muted:#4a5860;
  --pale:#eef2f5;
  --line:#d9dfe3;
  --white:#ffffff;
}
*{margin:0;padding:0;box-sizing:border-box}
html,body{width:833px;height:1200px;overflow:hidden;background:var(--white);font-family:'Lato',sans-serif;color:var(--ink)}
.page{position:relative;width:833px;height:1200px}

/* header */
.site-header{position:absolute;left:0;top:0;width:833px;height:87px;background:#f7f9fa;border-bottom:2px solid #5d6b73}
.brand{position:absolute;left:128px;top:26px;display:flex;align-items:center;gap:8px}
.brand-mark{width:22px;height:22px;background:var(--yellow)}
.brand-name{font-weight:900;font-size:28px;color:var(--navy);letter-spacing:1px}
.lang{position:absolute;right:105px;top:4px;font-size:8px;color:var(--muted);display:flex;align-items:center;gap:5px}
.lang i{display:inline-block;width:10px;height:7px;background:#b5c3d6}
.main-nav{position:absolute;right:26px;top:32px;display:flex;align-items:center;gap:17px;font-size:15px;color:var(--navy)}
.main-nav .active{position:relative}
.main-nav .active::after{content:"";position:absolute;left:-11px;right:-11px;top:49px;height:3px;background:var(--yellow)}
.caret{font-size:9px;margin-left:4px}
.search{width:21px;height:21px;border-radius:50%;background:var(--yellow);display:flex;align-items:center;justify-content:center}

/* hero */
.hero{position:absolute;left:0;top:87px;width:833px;height:286px;overflow:hidden}
.hero-photo{position:absolute;inset:0;background:
  linear-gradient(180deg,rgba(255,255,255,.25) 0%,rgba(255,255,255,0) 40%,rgba(40,40,40,.12) 100%),
  linear-gradient(90deg,#2a2824 0%,#5d5546 9%,#8f8168 16%,#4c63a0 24%,#3e5794 34%,#9aa8b8 44%,#d3dbe3 56%,#e2e8ee 72%,#cfd8e0 88%,#b9c4ce 100%)}
.hero-copy{position:absolute;left:417px;top:75px;width:320px}
.hero-copy h1{font-size:24px;font-weight:700;color:var(--navy);line-height:32px}
.hero-copy p{font-size:12px;color:var(--ink);line-height:16px;margin-top:4px}
.hero-arrow{position:absolute;top:126px;width:33px;height:33px;display:flex;align-items:center;justify-content:center}
.hero-arrow.prev{left:64px;border:1px solid #fff}
.hero-arrow.next{left:737px;background:var(--yellow)}
.dots{position:absolute;left:705px;top:270px;display:flex;gap:3px}
.dots span{width:5px;height:5px;border-radius:50%;background:#e4e8eb}
.dots span:first-child{background:var(--navy)}

/* welcome */
.welcome{position:absolute;left:0;top:373px;width:833px;height:167px;background:var(--pale);border-bottom:1px solid var(--line)}
.welcome h2{position:absolute;left:98px;top:44px;display:flex;align-items:center;gap:8px}
.welcome .tag{background:var(--yellow);font-weight:400;font-size:22px;color:var(--navy);padding:1px 6px 2px 6px;clip-path:polygon(4% 0,100% 0,96% 100%,0 100%)}
.welcome .name{font-weight:900;font-size:26px;color:var(--navy);letter-spacing:1px}
.welcome p{position:absolute;left:104px;top:86px;width:430px;font-size:9.5px;line-height:12px;color:var(--ink)}
.welcome-photo{position:absolute;left:556px;top:22px;width:176px;height:126px;background:linear-gradient(135deg,#f6d25a 0%,#f2bd1e 35%,#c93a35 65%,#8e2a2a 100%)}

/* services */
.services{position:absolute;left:0;top:540px;width:833px;height:165px;background:#f4f6f7;border-bottom:1px solid var(--line)}
.service{position:absolute;top:42px;width:200px;height:80px}
.service .icon{position:absolute;left:0;top:0;width:80px;height:80px;background:var(--yellow);border-bottom:4px solid var(--navy);display:flex;align-items:center;justify-content:center}
.service h3{position:absolute;left:86px;top:5px;font-size:12.5px;font-weight:700;color:var(--navy);white-space:nowrap}
.service p{position:absolute;left:86px;top:23px;width:112px;font-size:7.5px;line-height:12px;color:var(--muted)}
.service .more{position:absolute;left:86px;top:70px;font-size:8.5px;font-weight:700;color:var(--navy);display:flex;align-items:center;gap:6px;white-space:nowrap}
.service .more i{display:inline-block;width:20px;height:8px;background:var(--yellow);position:relative}
.service .more i::after{content:"";position:absolute;left:5px;top:3px;width:10px;height:2px;background:var(--navy)}

/* categories */
.categories{position:absolute;left:0;top:705px;width:833px;height:328px;background:var(--white)}
.categories h2{position:absolute;left:0;right:0;top:32px;text-align:center;font-size:16px;font-weight:400;color:var(--navy)}
.categories .rule{position:absolute;left:325px;top:57px;width:192px;height:1px;background:var(--yellow)}
.categories .lead{position:absolute;left:200px;width:433px;top:65px;text-align:center;font-size:8.5px;line-height:12px;color:var(--muted)}
.cat{position:absolute;top:108px;width:147px;height:137px;border:1px solid var(--yellow);background:#f9fafb}
.cat .thumb{position:absolute;left:0;right:0;top:0;height:119px}
.cat .label{position:absolute;left:0;right:0;bottom:0;height:17px;background:var(--yellow);font-size:9px;text-align:center;line-height:17px;color:var(--navy)}
.pager{position:absolute;left:104px;top:262px;width:627px;height:20px}
.pager .l{position:absolute;top:9px;height:1px;background:var(--yellow)}
.pager b{position:absolute;top:0;width:19px;height:19px;border-radius:50%;display:flex;align-items:center;justify-content:center}

/* footer */
.site-footer{position:absolute;left:0;top:1033px;width:833px;height:141px;background:var(--pale)}
.foot-brand{position:absolute;left:104px;top:20px;display:flex;align-items:center;gap:8px}
.foot-brand .brand-mark{width:18px;height:18px}
.foot-brand .brand-name{font-size:24px}
.foot-about{position:absolute;left:104px;top:72px;width:200px;font-size:7.5px;line-height:12px;color:var(--ink)}
.col h4{font-size:9.5px;font-weight:400;color:var(--navy);padding-bottom:8px;border-bottom:1px solid #e9d7b2;margin-bottom:7px}
.col{position:absolute;top:20px}
.col ul{list-style:none;font-size:7.5px;line-height:12px;color:var(--ink)}
.contact-line{display:flex;gap:5px;font-size:7.5px;line-height:12px;margin-bottom:10px}
.social{display:flex;gap:5px;margin-bottom:12px}
.social span{width:20px;height:20px;background:var(--navy)}
.newsletter{display:flex;margin-top:7px}
.newsletter .field{width:107px;height:23px;border:1px solid var(--navy);background:#fff;font-size:7.5px;padding:7px 6px}
.newsletter .btn{width:40px;height:23px;background:var(--navy);color:var(--yellow);font-size:9px;font-weight:700;display:flex;align-items:center;justify-content:center}
.bottom-bar{position:absolute;left:0;top:1174px;width:833px;height:26px;background:#d4dde3;font-size:8px;color:var(--ink)}
.bottom-bar .copy{position:absolute;left:104px;top:9px}
.bottom-bar nav{position:absolute;right:104px;top:9px;display:flex;gap:10px}
</style>
</head>
<body>
<div class="page">

<header class="site-header">
  <div class="brand"><span class="brand-mark"></span><span class="brand-name">VELTAR</span></div>
  <div class="lang">Select language <i></i></div>
  <nav class="main-nav">
    <span class="active">Home</span>
    <span>Products<span class="caret">&#9660;</span></span>
    <span>Blog</span>
    <span>About Us</span>
    <span>Contact</span>
    <span class="search"><svg width="10" height="10" viewBox="0 0 10 10"><circle cx="4" cy="4" r="3" fill="none" stroke="#163a4c" stroke-width="1.6"/><line x1="6.2" y1="6.2" x2="9" y2="9" stroke="#163a4c" stroke-width="1.8"/></svg></span>
  </nav>
</header>

<section class="hero">
  <div class="hero-photo" role="img" aria-label="Construction worker in yellow hard hat, safety glasses and blue shirt on a building site"></div>
  <div class="hero-copy">
    <h1>Lorem Ipsum Dolor Sit Amet<br>Sed ut perspiciatis unde</h1>
    <p>Itaque earum rerum hic tenetur a sapiente delectus. Nemo enim ipsam voluptatem quia voluptas sit aspernatur aut odit aut fugit.</p>
  </div>
  <div class="hero-arrow prev"><svg width="8" height="12"><polyline points="6,1 1,6 6,11" fill="none" stroke="#fff" stroke-width="1.5"/></svg></div>
  <div class="hero-arrow next"><svg width="8" height="12"><polyline points="2,1 7,6 2,11" fill="none" stroke="#163a4c" stroke-width="1.5"/></svg></div>
  <div class="dots"><span></span><span></span><span></span></div>
</section>

<section class="welcome">
  <h2><span class="tag">Welcome to</span><span class="name">VELTAR</span></h2>
  <p>Ut aut reiciendis voluptatibus maiores alias consequatur aut perferendis doloribus asperiores repellat. Facere possimus, omnis voluptas assumenda est, omnis dolor repellendus. Animi, id est laborum et dolorum fuga. Facere possimus, omnis voluptas assumenda est, omnis dolor repellendus.</p>
  <div class="welcome-photo" role="img" aria-label="Yellow hard hat beside a red tool bag full of tools and gloves"></div>
</section>

<section class="services">
  <div class="service" style="left:104px">
    <div class="icon"><svg width="34" height="34" viewBox="0 0 34 34"><line x1="6" y1="28" x2="26" y2="8" stroke="#163a4c" stroke-width="4"/><line x1="8" y1="8" x2="28" y2="28" stroke="#163a4c" stroke-width="4"/><rect x="3" y="3" width="10" height="6" fill="#163a4c" transform="rotate(45 8 6)"/></svg></div>
    <h3>Tool Division</h3>
    <p>Ut aut reiciendis voluptatibus maiores alias consequatur aut perferendis. Ut aut reiciendis voluptatibus maiores alias.</p>
    <span class="more">Read More <i></i></span>
  </div>
  <div class="service" style="left:317px">
    <div class="icon"><svg width="34" height="34" viewBox="0 0 34 34"><path d="M7 15 A10 10 0 0 1 27 15 Z" fill="#163a4c"/><rect x="5" y="15" width="24" height="3" fill="#163a4c"/><path d="M4 33 Q17 20 30 33 Z" fill="#163a4c"/></svg></div>
    <h3>Industrial Protection</h3>
    <p>Ut aut reiciendis voluptatibus maiores alias consequatur aut perferendis. Ut aut reiciendis voluptatibus maiores alias.</p>
    <span class="more">Read More <i></i></span>
  </div>
  <div class="service" style="left:530px">
    <div class="icon"><svg width="36" height="30" viewBox="0 0 36 30"><rect x="12" y="2" width="12" height="6" fill="none" stroke="#163a4c" stroke-width="2.5"/><rect x="2" y="7" width="32" height="22" rx="3" fill="#163a4c"/><rect x="16" y="12" width="4" height="12" fill="#f9ae1d"/><rect x="12" y="16" width="12" height="4" fill="#f9ae1d"/></svg></div>
    <h3>Health Protection</h3>
    <p>Ut aut reiciendis voluptatibus maiores alias consequatur aut perferendis. Ut aut reiciendis voluptatibus maiores alias.</p>
    <span class="more">Read More <i></i></span>
  </div>
</section>

<section class="categories">
  <h2>Our Products Categories</h2>
  <div class="rule"></div>
  <p class="lead">Ut aut reiciendis voluptatibus maiores alias consequatur aut perferendis doloribus asperiores repellat. Facere possimus, omnis voluptas assumenda est.</p>
  <div class="cat" style="left:104px"><div class="thumb" role="img" aria-label="Yellow safety helmet" style="background:linear-gradient(160deg,#fbfcfd 0%,#fbe7a0 45%,#f5c21f 100%)"></div><div class="label">Head Protection</div></div>
  <div class="cat" style="left:264px"><div class="thumb" role="img" aria-label="Pair of dark leather work gloves" style="background:linear-gradient(160deg,#fbfcfd 0%,#b7aea6 45%,#3f3631 100%)"></div><div class="label">Hands Protection</div></div>
  <div class="cat" style="left:424px"><div class="thumb" role="img" aria-label="Safety goggles and ear defenders" style="background:linear-gradient(160deg,#fbfcfd 0%,#c4cacd 45%,#2d3133 100%)"></div><div class="label">Eye &amp; Ear Protection</div></div>
  <div class="cat" style="left:584px"><div class="thumb" role="img" aria-label="Welding helmet" style="background:linear-gradient(160deg,#fbfcfd 0%,#b6bccb 45%,#1f2534 100%)"></div><div class="label">Welding Protection</div></div>
  <div class="pager">
    <span class="l" style="left:0;width:286px"></span>
    <b style="left:290px;background:#8c9aa3"><svg width="6" height="8"><polyline points="5,1 1,4 5,7" fill="none" stroke="#f9ae1d" stroke-width="1.5"/></svg></b>
    <b style="left:317px;background:var(--navy)"><svg width="6" height="8"><polyline points="1,1 5,4 1,7" fill="none" stroke="#f9ae1d" stroke-width="1.5"/></svg></b>
    <span class="l" style="left:342px;width:285px"></span>
  </div>
</section>

<footer class="site-footer">
  <div class="foot-brand"><span class="brand-mark"></span><span class="brand-name">VELTAR</span></div>
  <p class="foot-about">Architecto beatae vitae dicta sunt explicabo. Non numquam eius modi tempora incidunt ut labore et dolore magnam aliquam quaerat voluptatem.</p>
  <div class="col" style="left:317px;width:94px">
    <h4>Useful Links</h4>
    <ul><li>Contact Us</li><li>Our Distribution Policy</li><li>Useful Links</li><li>Express Service</li><li>Advanced Site Search</li><li>Site Map</li></ul>
  </div>
  <div class="col" style="left:424px;width:147px">
    <h4>Contact Info</h4>
    <div class="contact-line"><svg width="7" height="10" viewBox="0 0 7 10"><path d="M3.5 10 L0.5 4.5 A3 3 0 1 1 6.5 4.5 Z" fill="#163a4c"/><circle cx="3.5" cy="3.5" r="1.2" fill="#eef2f5"/></svg><span>418 Kestrel Lane, Harrow Vale,<br>Nairobi 00100</span></div>
    <div class="contact-line" style="margin-bottom:0"><svg width="8" height="8" viewBox="0 0 8 8"><path d="M1 1 L3 1 L3.5 3 L2.5 3.8 Q3.5 5.5 4.5 5.5 L5 4.5 L7 5 L7 7 Q2 7.5 1 1 Z" fill="#163a4c"/></svg><span>1-555-014-2290</span></div>
    <div class="contact-line"><svg width="9" height="7" viewBox="0 0 9 7"><rect width="9" height="7" fill="#163a4c"/><polyline points="0,0 4.5,4 9,0" fill="none" stroke="#eef2f5" stroke-width="1"/></svg><span>support@veltar.com</span></div>
  </div>
  <div class="col" style="left:584px;width:147px">
    <h4>Follow us</h4>
    <div class="social"><span></span><span></span><span></span><span></span><span></span></div>
    <div style="font-size:9.5px;color:var(--navy)">Sign Up for our Newsletters</div>
    <div class="newsletter"><span class="field">You Email Address..</span><span class="btn">Sign Up</span></div>
  </div>
</footer>

<div class="bottom-bar">
  <span class="copy">COPYRIGHT © 2013. VELTAR</span>
  <nav><span>Home</span><span>Products</span><span>Blog</span><span>About Us</span><span>Contact</span></nav>
</div>

</div>
</body>
</html>
```